Bring me business with this creative business card

Design my new business card. I am looking for something different with an impact. People will take a look at this card & they will 1- see how different & creative I am, 2-understand what I do 3- Call me to meet me!

I make videos with a message, testimonials. I am dynamic, fun, creative & human. My new website is in construction but in the meantime you can check this old one: brightpath.ca & another one Tidebloom.com & tidebloom facebook page.
I make videos. sometimes with a cameraman, sometimes with my phone. As an ex Public Relations agent, the message is the most important thing for me. I want to make my clients shine! When they start with me they often remind me of a lamb, when I finish coaching them they are powerful like LIONS! That's why I need a powerful business card!

Target Market(s)

Entrepreneurs, solo entrepreneurs, small & medium companies & start ups. People i will meet while networking. People that need videos on their website & social Networks to get attention, to be visible. men & women. From 35 to 49 years old.
I am an ex Public relations agent. I used to send clients in traditional medias, now with videos they have more chances to be seen on google the new media. I do videos of the president, his team, his loyal clients saying how great the company is & expert videos like series so people can be seen for example every 1 st of every month with a short 2 minute video. Also with my 20 years in marketing & communications I can coach & give tips to anybody who needs it.
Target: anybody who would like my old website brightpath.ca & I also have another website but it will be off line soon: tidebloom.com could give you ideas.

Industry/Entity Type

Communications

Contact Information for Business Card

I am in Montreal,So the business cards have to be the usual size like we have in Montreal: 9 cm x 5 cm
Details:My text: Mathilde Tessier Communication coach/Chief Guide. "Creating Videos as unique as you" off: 514-555-0147 cell: 514-555-0183. tidebloom.com
mathilde@tidebloom.com logo facebook, youtube, instagram

Colors
f37122

Requirements
Must have
• Dynamic, happy. Orange. Be creative in the look but NOT the shape of the card. Easy to read. Big enough to read.
Should not have
• No funny shapes: no round, no square, just the usual. I love creative but NOT on shape.

```html
<!DOCTYPE html>
<html lang="en">
<head>
<meta charset="utf-8">
<title>Tidebloom Business Card</title>
<link href="https://fonts.googleapis.com/css2?family=Cinzel:wght@400;600&family=Lato:wght@400&family=Tinos:wght@700&display=swap" rel="stylesheet">
<style>
  :root {
    --backdrop: #2f2f2f;
    --card-white: #ffffff;
    --orange: #f37122;
    --orange-deep: #ea5b1a;
    --orange-warm: #f6951f;
    --amber: #f8b41c;
    --ink: #1e1e1e;
    --white: #ffffff;
  }
  * { margin: 0; padding: 0; box-sizing: border-box; }
  html, body { width: 1200px; height: 900px; overflow: hidden; }
  body { background: var(--backdrop); position: relative; font-family: "Lato", Arial, sans-serif; }

  .card { position: absolute; top: 170px; width: 347px; height: 561px; }
  .card--front { left: 259px; background: var(--card-white); text-align: center; }
  .card--back { left: 631px; overflow: hidden; }

  .brand-mark {
    position: absolute; left: 50%; top: 76px; width: 92px; height: 92px;
    margin-left: -46px; border-radius: 50%; background: var(--orange);
  }
  .brand-name {
    position: absolute; top: 208px; left: 0; right: 0;
    font-family: "Cinzel", Georgia, serif; font-weight: 600; font-size: 35px;
    letter-spacing: 1px; color: var(--orange-deep); line-height: 1;
  }

  .person-name {
    position: absolute; top: 342px; left: 0; right: 0;
    font-family: "Tinos", "Times New Roman", serif; font-weight: 700; font-size: 21px;
    color: var(--orange-deep); letter-spacing: 0.5px; line-height: 1;
  }
  .person-title {
    position: absolute; top: 367px; left: 0; right: 0;
    font-size: 15px; color: var(--ink); line-height: 1;
  }
  .divider {
    position: absolute; top: 403px; left: 88px; width: 172px; height: 1.5px;
    background: var(--orange);
  }
  .contact-icons {
    position: absolute; top: 426px; left: 0; right: 0;
    display: flex; justify-content: center; gap: 2px;
  }
  .contact-icons svg { width: 18px; height: 18px; }
  .contact-list {
    position: absolute; top: 445px; left: 0; right: 0;
    list-style: none; font-size: 15px; color: var(--ink); line-height: 20px;
  }

  .back-pattern {
    position: absolute; inset: 0;
    background:
      radial-gradient(ellipse at 50% 55%, var(--amber) 0%, rgba(248,180,28,0) 45%),
      linear-gradient(160deg, var(--orange-warm) 0%, var(--orange) 50%, var(--orange-warm) 100%);
  }
  .slogan {
    position: absolute; top: 132px; left: 0; right: 0; text-align: center;
    font-family: "Cinzel", Georgia, serif; font-weight: 400; color: var(--white);
    text-shadow: 2px 3px 4px rgba(0,0,0,0.45);
  }
  .slogan-line { display: block; font-size: 48px; line-height: 62px; letter-spacing: 0.5px; }
  .slogan-emphasis { display: block; margin-top: 22px; font-size: 90px; line-height: 90px; letter-spacing: 22px; padding-left: 22px; }
</style>
</head>
<body>
  <section class="card card--front">
    <div class="brand-mark"></div>
    <div class="brand-name">TIDEBLOOM</div>

    <div class="person-name">MATHILDE T</div>
    <div class="person-title">Communication Coach/Chief Guide</div>
    <div class="divider"></div>

    <div class="contact-icons">
      <svg viewBox="0 0 18 18" aria-label="Office phone"><circle cx="9" cy="9" r="9" fill="#f37122"/><path d="M5 7.5c0-1.5 8-1.5 8 0v1h-2.2v-1H7.2v1H5z M6 9.5h6l1 3H5z" fill="#fff"/></svg>
      <svg viewBox="0 0 18 18" aria-label="Mobile phone"><circle cx="9" cy="9" r="9" fill="#f37122"/><rect x="6" y="4" width="6" height="10" rx="1" fill="#fff"/><rect x="7" y="5.5" width="4" height="6" fill="#f37122"/></svg>
      <svg viewBox="0 0 18 18" aria-label="Email"><circle cx="9" cy="9" r="9" fill="#f37122"/><rect x="4.5" y="5.5" width="9" height="7" fill="#fff"/><path d="M4.5 5.5L9 9.5l4.5-4" fill="none" stroke="#f37122" stroke-width="1"/></svg>
      <svg viewBox="0 0 18 18" aria-label="Website"><circle cx="9" cy="9" r="9" fill="#f37122"/><circle cx="9" cy="9" r="4.5" fill="none" stroke="#fff" stroke-width="1.2"/><path d="M4.5 9h9M9 4.5c-2.5 3-2.5 6 0 9M9 4.5c2.5 3 2.5 6 0 9" fill="none" stroke="#fff" stroke-width="1"/></svg>
    </div>
    <ul class="contact-list">
      <li>514-555-0147</li>
      <li>514-555-0183</li>
      <li>mathilde@tidebloom.com</li>
      <li>www.tidebloom.com</li>
    </ul>
  </section>

  <section class="card card--back">
    <div class="back-pattern" role="img" aria-label="Low-poly faceted orange artwork filling the card back"></div>
    <h2 class="slogan">
      <span class="slogan-line">CREATING</span>
      <span class="slogan-line">VIDEOS AS</span>
      <span class="slogan-line">UNIQUE AS</span>
      <span class="slogan-emphasis">YOU</span>
    </h2>
  </section>
</body>
</html>
```